BOLD & MINIMALIST DESIGN NEEDED

We want a very bold but minimalistic business card design that is impactful and utilizes both sides of the business card. Our current logo is included for your use.

We want bold fonts and good use of negative space. We don't want the logo to overpower the design.

Target Market(s)

Professionals who are building new commercial buildings.

Industry/Entity Type

Construction

Contact Information for Business Card

Name, Title, email, office phone, cell phone, website

Font styles to use
Serif
Sans Serif

Requirements
Must have
• Bold design!

```html
<!DOCTYPE html>
<html lang="en">
<head>
<meta charset="utf-8">
<title>Ridgeline Build — Business Card</title>
<link href="https://fonts.googleapis.com/css2?family=Montserrat:wght@800&family=Fira+Sans:wght@400&display=swap" rel="stylesheet">
<style>
  :root {
    --backdrop: #2a2a2a;
    --card-dark: #161616;
    --card-light: #ffffff;
    --ink: #111111;
    --ink-soft: #2b2b2b;
    --accent: #7cc42a;
    --mark-on-dark: #5a5a5a;
  }
  * { margin: 0; padding: 0; box-sizing: border-box; }
  html, body {
    width: 1200px; height: 1122px; overflow: hidden;
    background: var(--backdrop);
  }
  .canvas {
    width: 1200px; height: 1122px;
    display: flex; flex-direction: column; align-items: center; justify-content: center;
    gap: 44px;
  }
  .card {
    width: 840px; height: 480px; border-radius: 36px;
    position: relative; overflow: hidden;
  }
  /* back side */
  .card--back {
    background: var(--card-dark);
    display: flex; align-items: center; justify-content: center;
  }
  .wordmark {
    font-family: "Montserrat", sans-serif; font-weight: 800;
    letter-spacing: 1px; white-space: nowrap;
    display: flex; align-items: center; gap: 14px;
  }
  .wordmark__box { width: 26px; height: 26px; background: var(--accent); }
  .card--back .wordmark { font-size: 58px; color: var(--mark-on-dark); }
  .card--back .wordmark__box { width: 40px; height: 40px; }

  /* front side */
  .card--front { background: var(--card-light); }
  .holder {
    position: absolute; left: 64px; top: 118px;
  }
  .holder__name {
    font-family: "Montserrat", sans-serif; font-weight: 800;
    font-size: 38px; color: var(--ink); letter-spacing: 0.5px;
    line-height: 1;
  }
  .holder__title {
    font-family: "Fira Sans", sans-serif; font-weight: 400;
    font-size: 20px; color: var(--accent); margin-top: 8px;
    letter-spacing: 0.5px;
  }
  .divider {
    position: absolute; left: 64px; right: 70px; top: 222px;
    height: 2px; background: var(--ink);
  }
  .contacts {
    position: absolute; left: 64px; top: 244px;
    list-style: none;
    font-family: "Fira Sans", sans-serif; font-size: 20px; color: var(--ink-soft);
  }
  .contacts__item { display: flex; align-items: center; gap: 14px; height: 34px; letter-spacing: 0.6px; }
  .contacts__icon { width: 18px; height: 18px; flex: none; }
  .card--front .wordmark {
    position: absolute; right: 70px; top: 150px;
    font-size: 40px; color: var(--ink);
  }
</style>
</head>
<body>
<main class="canvas">
  <section class="card card--back" aria-label="Card back">
    <div class="wordmark"><span class="wordmark__box"></span>RIDGELINE BUILD</div>
  </section>

  <section class="card card--front" aria-label="Card front">
    <div class="holder">
      <h1 class="holder__name">DANIEL REYES</h1>
      <p class="holder__title">Founder &amp; CEO</p>
    </div>

    <div class="wordmark"><span class="wordmark__box"></span>RIDGELINE BUILD</div>

    <div class="divider"></div>

    <ul class="contacts">
      <li class="contacts__item">
        <svg class="contacts__icon" viewBox="0 0 24 24" fill="var(--accent)"><path d="M6.6 10.8a15.1 15.1 0 0 0 6.6 6.6l2.2-2.2a1 1 0 0 1 1-.25 11.4 11.4 0 0 0 3.6.57 1 1 0 0 1 1 1V20a1 1 0 0 1-1 1A17 17 0 0 1 3 4a1 1 0 0 1 1-1h3.5a1 1 0 0 1 1 1c0 1.25.2 2.45.57 3.57a1 1 0 0 1-.25 1z"/></svg>
        (555) 210-4480
      </li>
      <li class="contacts__item">
        <svg class="contacts__icon" viewBox="0 0 24 24" fill="none" stroke="var(--accent)" stroke-width="2.4"><rect x="6" y="2" width="12" height="20" rx="2"/><line x1="10" y1="18" x2="14" y2="18"/></svg>
        (555) 318-9026
      </li>
      <li class="contacts__item">
        <svg class="contacts__icon" viewBox="0 0 24 24" fill="var(--accent)"><path d="M2 5h20v14H2z"/><path d="M2 5l10 8 10-8" fill="none" stroke="#fff" stroke-width="1.8"/></svg>
        info@ridgelinebuild.com
      </li>
      <li class="contacts__item">
        <svg class="contacts__icon" viewBox="0 0 24 24" fill="none" stroke="var(--accent)" stroke-width="2.2"><circle cx="12" cy="12" r="9.5"/><ellipse cx="12" cy="12" rx="4" ry="9.5"/><line x1="2.5" y1="12" x2="21.5" y2="12"/></svg>
        ridgelinebuild.com
      </li>
    </ul>
  </section>
</main>
</body>
</html>
```